Business Card Design for Varomir Facility Services

We are looking for a Business Card Design for the Company "Varomir Facility Services."
Front side:
- Company Logo (small)
- Company Name, address, pohone, website and personal data.
- white background, for text e.g. company colors (blue or green like in the logo)
Please use following data:
Company data:
Varomir Facility Services Kostelac
Birkenhaldweg 14
6412 Farnbach
www.varomir-fs.ch
Person data:
Tarik Kostelac
Geschäftsführer
+41 76 519 47 83
info@varomir-fs.ch
Back side:
could be colored in blue or green
please use a big logo sing and some smaller icons to say what is all beeing offered in facility services, like cleaning, maintenance cleaning
industrial cleaning, caretaking, gardening, disposal. There is no need for everyone of the icons if there are similar or an icon is standing for more of them.
colors to use:
blue: HEX 246BB0
green: HEX 52B33E

```html
<!DOCTYPE html>
<html lang="de">
<head>
<meta charset="utf-8">
<title>Varomir Facility Services – Visitenkarte</title>
<link href="https://fonts.googleapis.com/css2?family=Roboto:wght@400;500;700;900&display=swap" rel="stylesheet">
<style>
  :root{
    --blue:#246BB0;
    --green:#52B33E;
    --green-line:#2FAE3A;
    --ink:#1c1c1c;
    --stage:#e9eaec;
    --white:#ffffff;
  }
  *{box-sizing:border-box;margin:0;padding:0}
  html,body{width:1200px;height:1200px;overflow:hidden;background:var(--stage)}
  body{font-family:"Roboto",Arial,sans-serif;position:relative}
  .card{position:absolute;left:160px;width:880px;height:500px;border-radius:28px;overflow:hidden;
        box-shadow:0 6px 18px rgba(0,0,0,.18)}
  .card--back{top:70px;background:var(--blue);color:var(--white)}
  .card--front{top:630px;background:var(--white)}

  /* back side */
  .brand-lockup{position:absolute;top:70px;left:0;right:0;text-align:center}
  .brand-lockup__mark{display:inline-block;width:34px;height:34px;border-radius:50%;background:var(--white);vertical-align:middle;margin-right:16px;position:relative;top:-10px}
  .brand-lockup__name{display:inline-block;font-weight:700;font-size:86px;letter-spacing:6px;line-height:1;vertical-align:middle}
  .brand-lockup__sub{display:block;font-weight:700;font-size:30px;letter-spacing:9px;margin-top:14px}
  .services{position:absolute;left:0;right:0;top:290px;display:flex;justify-content:center;gap:54px}
  .service{width:120px;text-align:center}
  .service__badge{width:96px;height:96px;margin:0 auto;border-radius:50%;background:var(--white);
        display:flex;align-items:center;justify-content:center;box-shadow:inset 0 0 0 4px var(--white),inset 0 0 0 6px var(--blue)}
  .service__badge svg{width:54px;height:54px}
  .service__label{font-weight:700;font-size:14px;line-height:1.15;margin-top:10px;letter-spacing:.3px}

  /* front side */
  .front-brand{position:absolute;left:60px;top:120px;width:330px;text-align:center}
  .front-brand__name{font-weight:700;font-size:58px;letter-spacing:4px;color:var(--blue);line-height:1}
  .front-brand__sub{font-weight:700;font-size:21px;letter-spacing:6px;color:var(--blue);margin-top:10px}
  .divider{position:absolute;left:420px;top:110px;width:2px;height:240px;background:var(--blue)}
  .contact{position:absolute;left:450px;top:110px;color:var(--ink)}
  .contact__name{font-weight:700;font-size:32px;color:var(--blue);line-height:1.05}
  .contact__role{font-size:16px;margin-top:2px}
  .contact__company{font-weight:700;font-size:20px;color:var(--green);margin-top:12px}
  .contact__address{font-size:20px;line-height:1.2;margin-top:4px}
  .contact__list{list-style:none;margin-top:8px;font-size:20px;line-height:1.3}
  .contact__list li{display:flex;align-items:center;gap:10px}
  .contact__list svg{width:17px;height:17px;flex:none}
  .contact__web-accent{color:var(--blue);font-weight:500}
  .wave{position:absolute;left:0;top:0;width:880px;height:500px}
</style>
</head>
<body>

<section class="card card--back" aria-label="Rückseite">
  <div class="brand-lockup">
    <span class="brand-lockup__mark"></span><span class="brand-lockup__name">VAROMIR</span>
    <span class="brand-lockup__sub">FACILITY SERVICES</span>
  </div>
  <div class="services">
    <div class="service">
      <div class="service__badge">
        <svg viewBox="0 0 54 54" fill="none" stroke="#246BB0" stroke-width="4" stroke-linecap="round" stroke-linejoin="round">
          <path d="M30 6 L27 24"/><rect x="14" y="24" width="26" height="8" rx="2" fill="#246BB0"/>
          <path d="M15 32 L13 48 M21 32 L20 48 M27 32 V48 M33 32 L34 48 M39 32 L41 48"/>
        </svg>
      </div>
      <div class="service__label">MAINTENANCE<br>CLEANING</div>
    </div>
    <div class="service">
      <div class="service__badge">
        <svg viewBox="0 0 54 54" fill="none" stroke="#246BB0" stroke-width="4" stroke-linejoin="round">
          <path d="M27 46 C10 34 5 24 8 16 C11 8 22 7 27 15 C32 7 43 8 46 16 C49 24 44 34 27 46 Z"/>
        </svg>
      </div>
      <div class="service__label">CARETAKING</div>
    </div>
    <div class="service">
      <div class="service__badge">
        <svg viewBox="0 0 54 54" fill="none" stroke="#246BB0" stroke-width="4" stroke-linecap="round" stroke-linejoin="round">
          <circle cx="27" cy="13" r="6"/><path d="M27 19 V32"/><path d="M27 27 C32 24 36 24 38 26"/>
          <path d="M15 32 H39 L36 48 H18 Z" fill="#246BB0"/>
        </svg>
      </div>
      <div class="service__label">GARDENING</div>
    </div>
    <div class="service">
      <div class="service__badge">
        <svg viewBox="0 0 54 54" fill="none" stroke="#246BB0" stroke-width="4" stroke-linecap="round" stroke-linejoin="round">
          <path d="M11 14 H43 M22 14 V9 H32 V14"/><path d="M14 18 H40 L37 48 H17 Z"/>
          <path d="M22 23 V43 M27 23 V43 M32 23 V43"/>
        </svg>
      </div>
      <div class="service__label">DISPOSAL</div>
    </div>
  </div>
</section>

<section class="card card--front" aria-label="Vorderseite">
  <svg class="wave" viewBox="0 0 880 500" aria-hidden="true">
    <path d="M0 318 C240 318 400 400 560 445 C680 478 780 462 880 460 L880 500 L0 500 Z" fill="#246BB0"/>
    <path d="M0 300 C230 298 370 340 470 392" fill="none" stroke="#2FAE3A" stroke-width="7"/>
    <path d="M690 446 C760 458 820 452 880 450" fill="none" stroke="#2FAE3A" stroke-width="6"/>
  </svg>

  <div class="front-brand">
    <div class="front-brand__name">VAROMIR</div>
    <div class="front-brand__sub">FACILITY SERVICES</div>
  </div>

  <div class="divider"></div>

  <div class="contact">
    <div class="contact__name">Tarik Kostelac</div>
    <div class="contact__role">Geschäftsführer</div>
    <div class="contact__company">Varomir Facility Services Kostelac</div>
    <div class="contact__address">Birkenhaldweg 14<br>6412 Farnbach</div>
    <ul class="contact__list">
      <li>
        <svg viewBox="0 0 24 24"><path fill="#246BB0" d="M6.6 10.8a15 15 0 0 0 6.6 6.6l2.2-2.2a1 1 0 0 1 1-.25 11.4 11.4 0 0 0 3.6.6 1 1 0 0 1 1 1V20a1 1 0 0 1-1 1A17 17 0 0 1 3 4a1 1 0 0 1 1-1h3.5a1 1 0 0 1 1 1c0 1.25.2 2.45.6 3.6a1 1 0 0 1-.25 1z"/></svg>
        +41 76 519 47 83
      </li>
      <li>
        <svg viewBox="0 0 24 24"><rect x="2" y="5" width="20" height="14" rx="2" fill="#246BB0"/><path d="M3 6 L12 13 L21 6" fill="none" stroke="#fff" stroke-width="2"/></svg>
        info@varomir-fs.ch
      </li>
      <li>
        <svg viewBox="0 0 24 24" fill="none" stroke="#246BB0" stroke-width="2"><circle cx="12" cy="12" r="9"/><path d="M3 12 H21 M12 3 C8 7 8 17 12 21 C16 17 16 7 12 3"/></svg>
        <span>www.<span class="contact__web-accent">varomir-fs</span>.ch</span>
      </li>
    </ul>
  </div>
</section>

</body>
</html>
```